Brell Stone Company Business Cards

Front and Back Business Card - logo and text setup - cool design. I need workable photoshop or illustrator files so I can setup each employee card with design that is created
Updates

Hi everyone, thank you for the great entries. Please no more white and blue cards - there are so many already - black and silver only now please. thanks!

Target Market(s)

Construction Industry - Facility Managers

Industry/Entity Type

Construction

Contact Information for Business Card

I really like contemporary simplistic looks - clean neat....not opposed to seeing some black backrounds

Requirements
Must have
• Logo/website address with design on front only - www.brellstone-example.com (logo attached)
• Back:
• Name/Title/Company Address/Phone/email address
Nice to have
• Cool design
Should not have
• Nothing gimmicky like Fire or Water - since we are a Fire Protection company - it has all been done

```html
<!DOCTYPE html>
<html lang="en">
<head>
<meta charset="utf-8">
<title>Brell Stone Company – Business Cards</title>
<link href="https://fonts.googleapis.com/css2?family=Lato:wght@400;700;900&display=swap" rel="stylesheet">
<style>
  :root {
    --page: #ffffff;
    --card: #101314;
    --silver: #c9cdd1;
    --silver-light: #eceef0;
    --silver-dark: #8b9196;
    --ink: #101314;
  }
  * { margin: 0; padding: 0; box-sizing: border-box; }
  html, body {
    width: 1200px; height: 1200px; overflow: hidden;
    background: var(--page);
    font-family: "Lato", sans-serif;
  }
  .card {
    position: absolute; left: 150px; width: 900px; height: 540px;
    background: var(--card);
  }
  .card--front { top: 55px; }
  .card--back { top: 608px; }

  .brand {
    position: absolute; left: 0; right: 0;
    display: flex; align-items: center; justify-content: center; gap: 18px;
  }
  .card--front .brand { top: 232px; }
  .card--back .brand { top: 108px; }
  .brand__mark { width: 34px; height: 34px; background: var(--silver-dark); }
  .brand__name {
    font-weight: 900; font-size: 66px; color: var(--silver-light);
    letter-spacing: -1px; line-height: 1;
  }

  .web-rule {
    position: absolute; left: 0; right: 0; top: 456px;
    display: flex; align-items: center; gap: 10px;
  }
  .web-rule__line { flex: 1; height: 3px; background: var(--silver-dark); }
  .web-rule__url {
    color: var(--silver); font-weight: 700; font-size: 19px; letter-spacing: 3px;
  }

  .person { position: absolute; left: 160px; top: 325px; }
  .person__name { font-weight: 700; font-size: 37px; line-height: 1; }
  .person__first { color: var(--silver-light); }
  .person__last { color: var(--silver-dark); }
  .person__title {
    display: inline-block; margin-top: 6px;
    color: var(--silver); font-size: 24px; line-height: 1.1;
    border-bottom: 3px solid var(--silver-dark); padding-bottom: 1px;
  }

  .divider {
    position: absolute; left: 437px; top: 296px;
    width: 3px; height: 136px; background: var(--silver-dark);
  }

  .contact { position: absolute; left: 469px; top: 287px; list-style: none; }
  .contact__item {
    display: flex; align-items: flex-start; gap: 10px;
    color: var(--silver); font-size: 22px; line-height: 1.35;
    margin-bottom: 8px;
  }
  .contact__icon {
    flex: none; width: 42px; height: 42px; border-radius: 50%;
    background: var(--silver); display: flex; align-items: center; justify-content: center;
  }
  .contact__text { padding-top: 8px; }
</style>
</head>
<body>

<section class="card card--front">
  <div class="brand">
    <span class="brand__mark"></span>
    <span class="brand__name">Brell Stone</span>
  </div>
  <div class="web-rule">
    <span class="web-rule__line"></span>
    <span class="web-rule__url">www.brellstone-example.com</span>
    <span class="web-rule__line"></span>
  </div>
</section>

<section class="card card--back">
  <div class="brand">
    <span class="brand__mark"></span>
    <span class="brand__name">Brell Stone</span>
  </div>

  <div class="person">
    <p class="person__name"><span class="person__first">Dana</span> <span class="person__last">Whitlock</span></p>
    <p class="person__title">Founder</p>
  </div>

  <span class="divider"></span>

  <ul class="contact">
    <li class="contact__item">
      <span class="contact__icon">
        <svg width="22" height="22" viewBox="0 0 24 24" aria-hidden="true"><path fill="#101314" d="M6.6 10.8a15.1 15.1 0 0 0 6.6 6.6l2.2-2.2c.3-.3.7-.4 1-.2 1.1.4 2.3.6 3.6.6.6 0 1 .4 1 1V20c0 .6-.4 1-1 1A17 17 0 0 1 3 4c0-.6.4-1 1-1h3.5c.6 0 1 .4 1 1 0 1.3.2 2.5.6 3.6.1.3 0 .7-.2 1z"/></svg>
      </span>
      <span class="contact__text">000-000-000</span>
    </li>
    <li class="contact__item">
      <span class="contact__icon">
        <svg width="22" height="18" viewBox="0 0 24 18" aria-hidden="true"><rect x="1" y="1" width="22" height="16" rx="2" fill="#101314"/><path d="M2 2l10 8 10-8" fill="none" stroke="#c9cdd1" stroke-width="2"/></svg>
      </span>
      <span class="contact__text">hello@brellstone-example.com</span>
    </li>
    <li class="contact__item">
      <span class="contact__icon">
        <svg width="18" height="24" viewBox="0 0 18 24" aria-hidden="true"><path fill="#101314" d="M9 0a9 9 0 0 0-9 9c0 6.8 9 15 9 15s9-8.2 9-15a9 9 0 0 0-9-9z"/><circle cx="9" cy="9" r="3.3" fill="#c9cdd1"/></svg>
      </span>
      <span class="contact__text">41 Harlow Street<br>Orlando, FL 32801</span>
    </li>
  </ul>
</section>

</body>
</html>
```